Biz Card

MARKETING today is the most rapidly changing business discipline. Media options to reach customers, actual customer preferences and consumer buying decisions change by the minute . . . no, by the second. The behavioral data generated by all aspects of the business and the new technologies that put the data to work together produce the potential to generate business intelligence and guide smart resource allocation to influence purchase and retention. However, to realize this potential, marketing professionals at all levels and in all organizations must continuously improve their skills not just from on-the-job training but by learning from masters in the field. The Bright Horizon Guild is the training center that serves this professional development need.model logos:msi.orgama.orgcontentmarketinginstitute.comBook covers on MarketingMetrics, Marketing Anaytics
Industry/Entity Type
Business
Contact Information for Business Card
Roy A. YoungCEOMarketing Science Academyphone: 310-601-4755email: roy@marketingscience.comAddress:437 South Rexford DriveBeverly Hills, CA 89377
Look and feel
Each slider illustrates characteristics of the customer's brand and the style your logo design should communicate.

```html
<!DOCTYPE html>
<html lang="en">
<head>
<meta charset="utf-8">
<title>Business Card – Bright Horizon Guild</title>
<link rel="stylesheet" href="https://fonts.googleapis.com/css2?family=Jost:wght@300;500&family=Open+Sans:wght@400;600&display=swap">
<style>
  :root {
    --page-bg: #c6c6c6;
    --card-navy: #0e3360;
    --band-navy: #06264a;
    --pattern-tone: #173f6f;
    --text-white: #ffffff;
    --text-soft: #e4ebf4;
  }
  * { box-sizing: border-box; margin: 0; padding: 0; }
  html, body {
    width: 1200px; height: 1200px; overflow: hidden;
    background: var(--page-bg);
  }
  .canvas {
    width: 1200px; height: 1200px;
    display: flex; align-items: center; justify-content: center;
  }
  .business-card {
    position: relative;
    width: 1050px; height: 600px;
    background: var(--card-navy);
    overflow: hidden;
  }
  .science-pattern {
    position: absolute; inset: 0;
    background:
      radial-gradient(ellipse at 20% 30%, var(--pattern-tone) 0%, transparent 45%),
      radial-gradient(ellipse at 85% 55%, var(--pattern-tone) 0%, transparent 40%);
    opacity: .8;
  }
  .identity {
    position: absolute; left: 0; right: 0; top: 150px;
    text-align: center; color: var(--text-white);
  }
  .person-name {
    font-family: "Open Sans", sans-serif; font-weight: 600;
    font-size: 34px; margin-left: 60px;
  }
  .job-title {
    font-family: "Jost", sans-serif; font-weight: 500;
    font-size: 150px; line-height: 1; margin-top: -6px; margin-left: 120px;
  }
  .company-name {
    font-family: "Jost", sans-serif; font-weight: 300;
    font-size: 50px; letter-spacing: 1px; text-transform: uppercase;
    color: var(--text-soft); margin-top: -4px; margin-left: 180px;
  }
  .contact-band {
    position: absolute; left: 0; right: 0; bottom: 34px; height: 100px;
    background: var(--band-navy);
    display: flex; align-items: center; justify-content: space-between;
    padding: 0 40px;
    font-family: "Open Sans", sans-serif; font-size: 25px;
    color: var(--text-white);
  }
  .contact-item { display: flex; align-items: center; gap: 14px; }
  .contact-item svg { flex: none; fill: var(--text-soft); }
  .address { line-height: 1.15; }
</style>
</head>
<body>
<main class="canvas">
  <section class="business-card">
    <div class="science-pattern" role="img" aria-label="Faint line drawings of laboratory flasks, molecules and chemical formulas"></div>

    <div class="identity">
      <p class="person-name">Neil P. Barton</p>
      <h1 class="job-title">CEO</h1>
      <p class="company-name">Bright Horizon Guild</p>
    </div>

    <footer class="contact-band">
      <div class="contact-item">
        <svg width="24" height="26" viewBox="0 0 24 24"><path d="M6.6 10.8a15 15 0 0 0 6.6 6.6l2.2-2.2a1 1 0 0 1 1-.25 11.4 11.4 0 0 0 3.6.57 1 1 0 0 1 1 1V20a1 1 0 0 1-1 1A17 17 0 0 1 3 4a1 1 0 0 1 1-1h3.5a1 1 0 0 1 1 1c0 1.25.2 2.45.57 3.57a1 1 0 0 1-.25 1z"/></svg>
        <span>310-555-0182</span>
      </div>
      <div class="contact-item">
        <svg width="40" height="28" viewBox="0 0 40 28"><rect x="1" y="1" width="38" height="26" fill="none" stroke="#e4ebf4" stroke-width="2.5"/><path d="M1 1l19 15L39 1" fill="none" stroke="#e4ebf4" stroke-width="2.5"/></svg>
        <span>neil@brighthorizonguild.com</span>
      </div>
      <div class="contact-item">
        <svg width="22" height="32" viewBox="0 0 22 32"><path d="M11 0A11 11 0 0 0 0 11c0 8 11 21 11 21s11-13 11-21A11 11 0 0 0 11 0zm0 15a4 4 0 1 1 0-8 4 4 0 0 1 0 8z"/></svg>
        <span class="address">912 North Calloway Lane<br>Beverly Hills, CA 89377</span>
      </div>
    </footer>
  </section>
</main>
</body>
</html>
```